Travel Agency Website - Simple General

Need a 7 page simple design that is pretty repetitive. Need to be able to load quickly that is SEO optimized. Trying to give ideas on what they can do, be personal as we are local, but at the same time come across as professional and get information easily with little burden.

- Landing Page
- Brimwell Vacations Page
- Family Trips
- Road Trips from Texas
- Other Destinations
- About Us Page
- Contact Us Page

Target Market(s)

Families

Coding

Coded - Design and coding required

Number of Pages Required

5+ page

Colors

Designer to choose colors to be used in the design.

Requirements
Must have
• Like it to flow easily with our logo. Use that for colors, etc.

```html
<!DOCTYPE html>
<html lang="en">
<head>
<meta charset="utf-8">
<title>Road Trips from Texas | Meander &amp; Hum Travel Co.</title>
<link href="https://fonts.googleapis.com/css2?family=Outfit:wght@300;400;500;600;700;800&display=swap" rel="stylesheet">
<style>
  :root{
    --teal:#1f5a64;
    --gold:#c49a4c;
    --gold-light:#d9b06a;
    --cream:#f6f3ee;
    --cream-row:#f3eee7;
    --ink:#2b3a3d;
    --line:#2d6670;
    --white:#ffffff;
    --sand:#d8c496;
    --olive:#7d8458;
  }
  *{box-sizing:border-box;margin:0;padding:0}
  html,body{width:865px;height:1200px;overflow:hidden}
  body{font-family:"Outfit",sans-serif;background:var(--cream);color:var(--teal);position:relative}
  a{text-decoration:none}
  .page{position:relative;width:865px;height:1200px;overflow:hidden;
    background:linear-gradient(180deg,#f4f1ec 0%,#f3f0ea 70%,#e9eeec 90%,#e4ebea 100%)}

  .hero-scene{position:absolute;left:330px;top:0;width:535px;height:465px;
    background:
      linear-gradient(90deg,var(--cream) 0%,rgba(246,243,238,0) 40%),
      linear-gradient(180deg,rgba(243,240,234,0) 75%,#f3f0ea 100%),
      linear-gradient(180deg,var(--sand) 0%,var(--olive) 100%);}

  .contact-bar{position:absolute;left:387px;top:0;width:402px;height:30px;background:var(--teal);
    border-radius:0 0 8px 8px;display:flex;align-items:center;gap:16px;padding-left:15px;color:var(--white);font-size:9.5px}
  .contact-bar .item{display:flex;align-items:center;gap:6px}
  .contact-bar .dot{width:18px;height:18px;border-radius:50%;background:var(--white);display:flex;align-items:center;justify-content:center}
  .contact-bar .phone-text{font-size:10.5px;font-weight:500}

  .brand{position:absolute;left:58px;top:40px;display:flex;align-items:center;gap:7px}
  .brand .mark{width:16px;height:16px;border-radius:50%;background:var(--gold)}
  .brand .name{font-size:17px;font-weight:600;color:var(--teal);line-height:1.1}

  .main-nav{position:absolute;top:53px;left:0;width:865px;font-size:10.5px;color:var(--teal)}
  .main-nav a{position:absolute;top:2px;color:var(--teal);white-space:nowrap}
  .main-nav a.current::after{content:"";position:absolute;left:1px;right:0;bottom:-8px;height:1.5px;background:var(--gold)}
  .main-nav .home{left:221px;top:3px}
  .main-nav .contact-btn{position:absolute;left:687px;top:-6px;width:98px;height:27px;border-radius:14px;background:var(--gold);
    color:var(--white);font-size:9.5px;display:flex;align-items:center;padding-left:18px}
  .contact-btn .arrow{position:absolute;right:5px;top:4px;width:19px;height:19px;border-radius:50%;background:var(--gold-light);display:flex;align-items:center;justify-content:center}

  .hero-copy{position:absolute;left:93px;top:162px;width:300px}
  .eyebrow{font-size:15px;font-weight:400;letter-spacing:.3px;color:var(--teal)}
  .hero-title{font-size:34px;font-weight:700;line-height:1.1;color:var(--teal);margin-top:6px;position:relative;display:inline-block}
  .sparkle{position:absolute;color:var(--gold);font-size:13px}
  .partner{display:flex;align-items:center;gap:9px;margin-top:10px;font-size:13px;color:var(--teal)}
  .partner .badge{width:20px;height:20px;border:1.3px solid var(--gold);border-radius:3px}
  .partner .partner-name{font-size:10.5px;font-weight:600;line-height:1.2}
  .hero-text{margin-top:14px;font-size:9.8px;line-height:1.45;color:var(--ink);width:252px}

  .table-wrap{position:absolute;left:82px;top:416px;width:721px;height:200px;border:1px solid #6f969b;border-radius:6px;overflow:hidden;background:var(--white)}
  .table-wrap table{width:100%;border-collapse:collapse;table-layout:fixed}
  .table-wrap th{background:var(--teal);color:var(--white);font-weight:500;font-size:10px;height:31px;text-align:left}
  .table-wrap td{height:42px;color:var(--teal);font-size:10.5px;font-weight:400}
  .table-wrap tbody tr:nth-child(even) td{background:var(--cream-row)}
  .c1{width:110px;padding-left:31px}.c1d{padding-left:34px}
  .c2{width:100px}.c3{width:98px}.c4{width:112px}.c5{width:84px}.c6{width:104px}

  .plan-card{position:absolute;left:80px;top:662px;width:721px;height:436px;border:1px solid #b9cccd;border-radius:6px;
    background:rgba(249,248,245,.85)}
  .plan-title{position:absolute;top:35px;left:0;width:100%;text-align:center;font-size:22px;font-weight:700;color:var(--teal)}
  .plan-title .sparkle{right:192px;top:-10px}
  .field-label{position:absolute;font-size:11.5px;font-weight:500;color:var(--teal)}
  .field{position:absolute;height:41px;border:1px solid var(--line);background:var(--white);display:flex;align-items:center;
    padding-left:17px;font-size:11px;color:var(--teal);font-weight:300}
  .field .chev{position:absolute;right:14px;top:14px}
  .field .cal{margin-right:9px;margin-left:-4px}
  .field.notes{height:80px;align-items:flex-start;padding-top:12px;padding-left:19px}
  .plan-btn{position:absolute;left:272px;top:365px;width:181px;height:38px;border-radius:19px;background:var(--gold);
    color:var(--white);font-size:14px;font-weight:600;display:flex;align-items:center;padding-left:42px}
  .plan-btn .arrow{position:absolute;right:6px;top:5px;width:28px;height:28px;border-radius:50%;background:var(--gold-light);display:flex;align-items:center;justify-content:center}

  .site-footer{position:absolute;left:0;top:1139px;width:865px;height:61px;background:var(--white)}
  .site-footer .copy{position:absolute;left:0;width:100%;top:16px;text-align:center;font-size:9.5px;color:var(--ink)}
  .social{position:absolute;left:721px;top:13px;display:flex;gap:5px}
  .social span{width:16px;height:16px;border-radius:50%;background:var(--teal)}
</style>
</head>
<body>
<div class="page">
  <div class="hero-scene" role="img" aria-label="Photo of a winding road through limestone cliffs and green Texas hills at sunset"></div>

  <div class="contact-bar">
    <div class="item"><span class="dot"><svg width="10" height="8" viewBox="0 0 10 8"><rect x=".5" y=".5" width="9" height="7" fill="none" stroke="#1f5a64"/><path d="M.5 .5 5 4.5 9.5 .5" fill="none" stroke="#1f5a64"/></svg></span>hello@meanderandhum.com</div>
    <div class="item"><span class="dot"><svg width="10" height="10" viewBox="0 0 24 24"><path fill="#1f5a64" d="M6.6 10.8a15 15 0 0 0 6.6 6.6l2.2-2.2c.3-.3.7-.4 1-.2 1.1.4 2.3.6 3.6.6.6 0 1 .4 1 1V20c0 .6-.4 1-1 1A17 17 0 0 1 3 4c0-.6.4-1 1-1h3.5c.6 0 1 .4 1 1 0 1.3.2 2.5.6 3.6.1.3 0 .7-.2 1z"/></svg></span><span class="phone-text">Phone Number (555) 218 4470</span></div>
  </div>

  <div class="brand"><span class="mark"></span><span class="name">Meander &amp; Hum</span></div>

  <nav class="main-nav">
    <a class="home" href="#" aria-label="Home"><svg width="10" height="9" viewBox="0 0 10 9"><path d="M5 0 0 4.5h1.3V9h2.5V6h2.4v3h2.5V4.5H10z" fill="#c49a4c"/></svg></a>
    <a href="#" style="left:247px">Brimwell Vacations</a>
    <a href="#" style="left:346px">Family Trips</a>
    <a href="#" class="current" style="left:418px">Texas Road Trips</a>
    <a href="#" style="left:515px">Other Destinations</a>
    <a href="#" style="left:631px">About Us</a>
    <a href="#" class="contact-btn">Contact Us<span class="arrow"><svg width="7" height="7" viewBox="0 0 7 7"><path d="M1 6 6 1M2 1h4v4" stroke="#fff" fill="none"/></svg></span></a>
  </nav>

  <section class="hero-copy">
    <p class="eyebrow">TEXAS ROAD TRIPS</p>
    <h1 class="hero-title">ROAD TRIPS<br>FROM TEXAS<span class="sparkle" style="left:213px;top:-6px">✦</span></h1>
    <div class="partner">In Partnership with <span class="badge"></span><span class="partner-name">PINECREST<br>VAN RENTAL</span></div>
    <p class="hero-text">Scenic routes. Unforgettable places. Epic adventures. Explore handpicked road trips perfect for families, couples, and adventure seekers.</p>
  </section>

  <div class="table-wrap">
    <table>
      <thead><tr><th class="c1">Trip Name</th><th class="c2">Duration</th><th class="c3">Best For</th><th class="c4">Destination</th><th class="c5">Total Price</th><th class="c6">Price per person</th><th>Van Rental</th></tr></thead>
      <tbody>
        <tr><td class="c1d">TRIP A</td><td>3 Days</td><td>Families</td><td>Big Bend</td><td>$125</td><td>$125</td><td>Included</td></tr>
        <tr><td class="c1d">TRIP B</td><td>5 Days</td><td>Couples</td><td>Hill Country</td><td>$250</td><td>$250</td><td>Optional</td></tr>
        <tr><td class="c1d">TRIP C</td><td>7 Days</td><td>Adventures</td><td>National Parks</td><td>$325</td><td>$325</td><td>Included</td></tr>
        <tr><td class="c1d">TRIP D</td><td>9 Days</td><td>Adventures</td><td>National Parks</td><td>$450</td><td>$450</td><td>Included</td></tr>
      </tbody>
    </table>
  </div>

  <section class="plan-card">
    <h2 class="plan-title">PLAN YOUR TEXAS ROAD TRIP<span class="sparkle">✦</span></h2>

    <label class="field-label" style="left:41px;top:88px">What Type of Trip Are You Interested In?</label>
    <div class="field" style="left:41px;top:114px;width:319px">Select<svg class="chev" width="12" height="8" viewBox="0 0 12 8"><path d="M1 1l5 5 5-5" stroke="#1f5a64" stroke-width="1.6" fill="none"/></svg></div>

    <label class="field-label" style="left:372px;top:88px">How Many People in Your Party?</label>
    <div class="field" style="left:370px;top:114px;width:155px">No. of Adults<svg class="chev" width="12" height="8" viewBox="0 0 12 8"><path d="M1 1l5 5 5-5" stroke="#1f5a64" stroke-width="1.6" fill="none"/></svg></div>
    <div class="field" style="left:532px;top:114px;width:155px">No. of Kids<svg class="chev" width="12" height="8" viewBox="0 0 12 8"><path d="M1 1l5 5 5-5" stroke="#1f5a64" stroke-width="1.6" fill="none"/></svg></div>

    <label class="field-label" style="left:41px;top:173px">Do you need a Van Rental?</label>
    <div class="field" style="left:41px;top:197px;width:319px">Yes<svg class="chev" width="12" height="8" viewBox="0 0 12 8"><path d="M1 1l5 5 5-5" stroke="#1f5a64" stroke-width="1.6" fill="none"/></svg></div>

    <label class="field-label" style="left:374px;top:173px">When Would You Like To Go?</label>
    <div class="field" style="left:371px;top:197px;width:155px;padding-left:13px"><svg class="cal" width="13" height="13" viewBox="0 0 13 13"><rect x=".5" y="2" width="12" height="10.5" fill="none" stroke="#9aaeb0"/><path d="M3 .5v3M10 .5v3M.5 5h12" stroke="#9aaeb0"/><path d="M3 7h1M6 7h1M9 7h1M3 9.5h1M6 9.5h1M9 9.5h1" stroke="#9aaeb0"/></svg>Start Date</div>
    <div class="field" style="left:533px;top:197px;width:155px;padding-left:13px"><svg class="cal" width="13" height="13" viewBox="0 0 13 13"><rect x=".5" y="2" width="12" height="10.5" fill="none" stroke="#9aaeb0"/><path d="M3 .5v3M10 .5v3M.5 5h12" stroke="#9aaeb0"/><path d="M3 7h1M6 7h1M9 7h1M3 9.5h1M6 9.5h1M9 9.5h1" stroke="#9aaeb0"/></svg>End Date</div>

    <label class="field-label" style="left:41px;top:248px">Any Additional Notes</label>
    <div class="field notes" style="left:41px;top:271px;width:648px">Type here</div>

    <a class="plan-btn" href="#">Start Planning<span class="arrow"><svg width="9" height="9" viewBox="0 0 9 9"><path d="M1 8 8 1M2.5 1H8v5.5" stroke="#fff" stroke-width="1.4" fill="none"/></svg></span></a>
  </section>

  <footer class="site-footer">
    <p class="copy">© 2026 Meander &amp; Hum. All Right Reserved</p>
    <div class="social"><span role="img" aria-label="Social link one"></span><span role="img" aria-label="Social link two"></span></div>
  </footer>
</div>
</body>
</html>
```